Design a Website in Wordpress for an Australian Health Training Company in Health related courses

We require a WORDPRESS based Website (due to add on's we need to use for third party software) to replace our old site.
We offer national face to face delivery in medical reception, terminology and also administration.
The website will have around 6 pages and the ability to describe our main 6 courses (perhaps on the Courses page this may be tabs opening up to details for example?)
I have attached a previous sample of a Joomla site which was being developed (please do not feel you have to copy this - but I am just giving it as a sample - copying would be boring). But it gives an idea of look/feel and colours which may be suitable. Open to other ideas though.
I will provide some of the content, but would like the ability to finish the content myself.
Images and graphics are important. While a few medical photos re great - don't be tempted to us all pictures of doctors and nurses (although a couple would be good) - these are administrative courses so general corporate, eye catching visionary pictures of people in general are great. A medical type picture is also fine.
THE BOOKING system - will be via an ADD ON which will occur at the end of the project and is supplied by a third party software company (our student management system). This project will include up to 2 hours working with the Tech guys from the third party software to enable the ADD ON. If this ADD ON requires more time, we will pay hourly (although I do not expect it will).
Target Market(s)
Mostly a female market, many mature aged women target 25-45 yrs. Mixture of medical/health and corporate. Maybe a bit of mums returning to work and corporate inspiration.
Industry/Entity Type
It Company
Coding
Coded - Design and coding required
Number of Pages Required
5+ page
Requirements
Must have
- Wordpress
- Great graphics
- Interesting
- professional and clean
- Enquiry section (info Pak)
- Should have a University feel to it - Education
- Pages
- Home Page - About Us - Recruitment -Courses - Class Schedule - Traineeships Queensland Funding - Latest News Blog - Corporate Training- Contact us

```html
<!DOCTYPE html>
<html lang="en">
<head>
<meta charset="utf-8">
<title>Calder Institute of Training</title>
<link href="https://fonts.googleapis.com/css2?family=Bitter:wght@400;500;700&family=Open+Sans:ital,wght@0,400;0,600;0,700;1,400;1,600&display=swap" rel="stylesheet">
<style>
:root{
  --navy:#2b3859;
  --navy-deep:#243150;
  --nav:#33446b;
  --orange:#e0902c;
  --ink:#3a3f4a;
  --line:#e3e6ec;
  --white:#ffffff;
}
*{box-sizing:border-box;margin:0;padding:0}
html,body{width:1200px;height:4072px;overflow:hidden}
body{font-family:"Open Sans",Arial,sans-serif;color:var(--ink);background:var(--white);font-size:13px;line-height:1.55}
section,header,nav,footer{position:relative;width:1200px}
.btn{display:inline-flex;align-items:center;justify-content:center;font-size:12px;font-weight:700;letter-spacing:.04em;color:var(--white);text-transform:uppercase;white-space:nowrap}
.btn-orange{background:var(--orange)}
.btn-navy{background:var(--navy-deep)}
.sec-title{font-family:"Bitter",Georgia,serif;font-size:28px;font-weight:400;text-align:center;color:#2e3344}

/* top bar */
.topbar{height:49px;background:var(--navy-deep);color:#d6dbe6;font-size:12px}
.topbar .item{position:absolute;top:0;height:49px;display:flex;align-items:center;gap:8px;white-space:nowrap}
.social{position:absolute;display:flex;gap:6px}
.social span{width:26px;height:26px;border-radius:50%;border:1.5px solid currentColor;display:block}

/* header */
.masthead{height:168px;background:var(--white)}
.brand{position:absolute;left:72px;top:62px;display:flex;align-items:center;gap:12px}
.brand .mark{width:34px;height:34px;background:var(--navy)}
.brand .name{font-family:"Open Sans",Arial,sans-serif;font-size:16px;font-weight:700;color:var(--navy);white-space:nowrap}
.masthead .btn{position:absolute;left:975px;width:150px;height:34px}

/* nav */
.mainnav{height:55px;background:var(--nav);display:flex;padding-left:65px}
.mainnav a{display:flex;align-items:center;padding:0 19px;color:var(--white);font-size:11.5px;font-weight:600;text-transform:uppercase;text-decoration:none;white-space:nowrap}
.mainnav a.active{background:var(--orange);padding:0 34px}
.mainnav a.more{margin-left:auto;margin-right:55px}

/* hero */
.hero{height:534px;overflow:hidden}
.hero-bg{position:absolute;inset:0;background:
  radial-gradient(ellipse 240px 300px at 930px 330px,rgba(255,255,255,.95),rgba(255,255,255,0) 70%),
  radial-gradient(ellipse 110px 120px at 930px 80px,rgba(214,196,184,.8),rgba(214,196,184,0) 70%),
  linear-gradient(100deg,#f1f3f7 0%,#e5e9ef 40%,#c3ccda 75%,#b3bdce 100%)}
.hero h1{position:absolute;left:75px;top:148px;font-family:"Bitter",Georgia,serif;font-weight:400;font-size:46px;color:#2a2f3d;white-space:nowrap}
.hero h1 em{font-style:normal;color:var(--orange)}
.hero p{position:absolute;left:75px;top:222px;width:600px;font-size:17px;font-weight:600;font-style:italic;color:#2e3344;line-height:1.5}
.hero .btn{position:absolute;left:75px;top:305px;width:170px;height:44px;font-size:13px}
.dots{position:absolute;left:566px;top:498px;display:flex;gap:14px}
.dots i{width:9px;height:9px;border-radius:50%;background:#b8bfcb}
.dots i.on{background:#3a4460}

/* welcome */
.welcome{height:302px;text-align:center}
.welcome .sec-title{padding-top:64px}
.welcome p{width:1060px;margin:26px auto 0;font-size:13px;color:#555c68;line-height:1.75}
.welcome .btn{margin-top:20px;width:130px;height:38px}

/* courses */
.courses{height:584px;background:linear-gradient(135deg,#2f3c60,#263352 60%,#2d3a5d);color:var(--white)}
.courses .sec-title{color:var(--white);padding-top:72px;font-size:30px}
.course-grid{position:absolute;left:60px;top:150px;width:1080px;display:grid;grid-template-columns:repeat(3,1fr)}
.course{height:196px;padding:20px 20px 0 16px;border-right:1px solid rgba(255,255,255,.14)}
.course:nth-child(3n){border-right:none}
.course:nth-child(-n+3){border-bottom:1px solid rgba(255,255,255,.14)}
.course .head{display:flex;align-items:center;gap:14px;min-height:56px}
.course h3{font-family:"Bitter",Georgia,serif;font-weight:400;font-size:19px;line-height:1.25;width:210px}
.course p{margin-top:10px;font-size:13px;color:#98a3bb;line-height:1.6;width:290px}
.course a{display:block;margin-top:8px;color:var(--orange);font-size:12px;font-weight:700;text-decoration:none}

/* why */
.why{height:602px}
.why .sec-title{padding-top:62px}
.feature{position:absolute;background:var(--white);border:1px solid var(--line);box-shadow:0 1px 3px rgba(0,0,0,.06);padding:14px 110px 0 20px}
.feature h3{font-family:"Bitter",Georgia,serif;font-weight:400;font-size:19px;color:var(--orange)}
.feature p{margin-top:6px;font-size:13px;font-style:italic;color:#444a56;line-height:1.55}
.feature svg{position:absolute;right:26px;top:50%;transform:translateY(-50%)}

/* blog */
.blog{height:619px;background:linear-gradient(160deg,#f2f3f5,#e6e8ec 50%,#f0f1f3)}
.blog .sec-title{padding-top:76px}
.blog-box{position:absolute;left:75px;top:161px;width:1052px;height:375px;border:1px solid #c9ccd3;background:rgba(255,255,255,.35)}
.scroll{position:absolute;right:0;top:0;width:14px;height:100%;background:#d9dce2}
.scroll i{position:absolute;left:3px;top:8px;width:8px;height:80px;background:#9da3ae;border-radius:4px}
.post{position:absolute;width:320px;height:158px;background:var(--white);box-shadow:0 1px 3px rgba(0,0,0,.08);padding:14px 14px 0 14px}
.post .thumb{position:absolute;left:14px;top:16px;width:64px;height:64px;background:linear-gradient(135deg,#c9b8a6,#e9ddd0)}
.post .body{margin-left:80px}
.post h4{font-family:"Bitter",Georgia,serif;font-weight:400;font-size:16px;color:var(--orange)}
.post p{font-size:12.5px;color:#555;line-height:1.5;margin-top:4px}
.post .meta{margin-top:8px;font-size:11px;color:var(--orange);display:flex;gap:18px}

/* enquiry */
.enquiry{height:331px;overflow:hidden}
.enquiry-bg{position:absolute;inset:0;background:linear-gradient(100deg,#d9892b,#e8a347 50%,#d38530)}
.enquiry .sec-title{position:relative;color:var(--white);padding-top:60px}
.field{position:absolute;width:244px;height:40px;background:var(--white);display:flex;align-items:center;gap:10px;padding-left:14px;font-size:12px;color:#666}
.field i{width:10px;height:10px;border:1.5px solid #999;border-radius:2px}
.enquiry .btn{position:absolute;left:735px;top:211px;width:244px;height:40px}

/* testimonials */
.testimonials{height:348px}
.testimonials .sec-title{padding-top:60px}
.quote{position:absolute;left:165px;top:111px;width:870px;height:92px;background:var(--white);box-shadow:0 1px 4px rgba(0,0,0,.1);padding:14px 40px;font-size:12.5px;font-style:italic;text-align:center;color:#444;line-height:1.65}
.person{position:absolute;left:0;width:1200px;top:232px;display:flex;align-items:center;justify-content:center;gap:16px}
.person .avatar{width:62px;height:62px;border-radius:50%;background:linear-gradient(135deg,#e6c7a8,#f3e2d0)}
.person .name{font-size:13px;font-weight:700;color:var(--orange);text-transform:uppercase}
.arrow{position:absolute;top:250px;font-size:20px;color:#555}

/* footer */
.footer{height:480px;background:var(--navy);color:#c4cbd9}
.col{position:absolute;top:56px}
.col h5{font-family:"Bitter",Georgia,serif;font-weight:400;font-size:19px;color:var(--white);text-transform:uppercase;letter-spacing:.02em}
.col p,.col li{font-size:12.5px;line-height:1.6;color:#a9b3c6;list-style:none}
.col .date{color:var(--white);font-size:11px;font-weight:700;margin:6px 0 18px}
.foot-brand{margin-top:22px;display:flex;align-items:center;gap:10px}
.foot-brand .mark{width:26px;height:26px;border:1.5px solid var(--white)}
.foot-brand .name{font-family:"Open Sans",Arial,sans-serif;font-weight:700;font-size:13px;color:var(--white);white-space:nowrap}
.newsletter{display:flex;margin-top:14px}
.newsletter .input{width:180px;height:38px;background:var(--white);font-size:12px;color:#666;display:flex;align-items:center;padding-left:12px}
.newsletter .go{width:38px;height:38px;background:var(--navy-deep);display:flex;align-items:center;justify-content:center}
.copyright{position:absolute;left:0;bottom:0;width:1200px;height:62px;border-top:1px solid rgba(255,255,255,.12);display:flex;align-items:center;justify-content:center;font-size:12px;color:#8f99ad}
</style>
</head>
<body>

<div class="topbar">
  <div class="item" style="left:40px">
    <svg width="14" height="14" viewBox="0 0 14 14" fill="none" stroke="#d6dbe6" stroke-width="1.3"><circle cx="7" cy="7" r="6"/><path d="M1 7h12M7 1c2 2 2 10 0 12M7 1c-2 2-2 10 0 12"/></svg>
    English ▾
  </div>
  <div class="item" style="left:212px">
    <svg width="11" height="14" viewBox="0 0 11 14"><path d="M5.5 0C2.5 0 0 2.3 0 5.3 0 9 5.5 14 5.5 14S11 9 11 5.3C11 2.3 8.5 0 5.5 0zm0 7.4a2 2 0 110-4 2 2 0 010 4z" fill="#d6dbe6"/></svg>
    12 Harbour Row, Brisbane QLD
  </div>
  <div class="item" style="left:470px">
    <svg width="11" height="13" viewBox="0 0 11 13"><rect x="0" y="5.5" width="11" height="7.5" rx="1" fill="#d6dbe6"/><path d="M2.5 5.5V4a3 3 0 016 0v1.5" stroke="#d6dbe6" stroke-width="1.4" fill="none"/></svg>
    Log in / Register
  </div>
  <div class="social" style="left:1005px;top:11px;color:#d6dbe6"><span></span><span></span><span></span><span></span></div>
</div>

<header class="masthead">
  <div class="brand">
    <div class="mark"></div>
    <div class="name">Calder Institute of Training</div>
  </div>
  <a class="btn btn-orange" style="top:48px">
    <svg width="12" height="14" viewBox="0 0 12 14" style="margin-right:10px"><path d="M6 0v9M2 5l4 4 4-4M0 13h12" stroke="#fff" stroke-width="1.6" fill="none"/></svg>Enrol Now</a>
  <a class="btn btn-navy" style="top:96px">
    <svg width="12" height="14" viewBox="0 0 12 14" style="margin-right:10px"><path d="M1 0h7l3 3v11H1z" fill="#fff"/></svg>Info Pack</a>
</header>

<nav class="mainnav">
  <a class="active">Home</a>
  <a>About Us</a>
  <a>Recruitment</a>
  <a>Courses</a>
  <a>Class Schedule</a>
  <a>Traineeships Queensland Funding</a>
  <a>Latest News Blog</a>
  <a class="more">More</a>
</nav>

<section class="hero">
  <div class="hero-bg" role="img" aria-label="Photo of a smiling medical professional in a white coat on a soft grey-blue background, gesturing toward the headline"></div>
  <h1>Cources for <em>busy people</em></h1>
  <p>Calder is a Registered Training Organisation offering specialised Medical Administration Training in over 15 locations Australia wide.</p>
  <a class="btn btn-orange">Booking Now</a>
  <div class="dots"><i class="on"></i><i></i><i></i></div>
</section>

<section class="welcome">
  <h2 class="sec-title">Welcome to Our Site</h2>
  <p>Calder is Australia's Leading Provider of Educational, Training and Support Services for the Medical and Dental industry - enabling students to be immediately skilled and 'Job Ready' for a career in Health. Calder is a Registered Training Organisation offering specialised Medical Administration Training in over 15 locations Australia wide. Calder have trained thousands of students the required knowledge and skills to become successful health care administrators.</p>
  <a class="btn btn-orange">Read More</a>
</section>

<section class="courses">
  <h2 class="sec-title">List Of Cources</h2>
  <div class="course-grid">
    <div class="course"><div class="head"><svg width="30" height="30" viewBox="0 0 30 30"><circle cx="15" cy="15" r="13" fill="none" stroke="#e0902c" stroke-width="3"/><path d="M9 15l4.5 4.5L21.5 11" stroke="#e0902c" stroke-width="3" fill="none"/></svg><h3>Medical Reception &amp; Terminology</h3></div><p>Neque porro quisquam est qui dolorem ipsum quia dolor sit amet, consectetur velit.</p><a>READ MORE</a></div>
    <div class="course"><div class="head"><svg width="30" height="30" viewBox="0 0 30 30"><circle cx="15" cy="15" r="13" fill="none" stroke="#e0902c" stroke-width="3"/><path d="M9 15l4.5 4.5L21.5 11" stroke="#e0902c" stroke-width="3" fill="none"/></svg><h3>Cert III Business Administration</h3></div><p>Neque porro quisquam est qui dolorem ipsum quia dolor sit amet, consectetur velit.</p><a>READ MORE</a></div>
    <div class="course"><div class="head"><svg width="30" height="30" viewBox="0 0 30 30"><circle cx="15" cy="15" r="13" fill="none" stroke="#e0902c" stroke-width="3"/><path d="M9 15l4.5 4.5L21.5 11" stroke="#e0902c" stroke-width="3" fill="none"/></svg><h3>Medical Terminology</h3></div><p>Neque porro quisquam est qui dolorem ipsum quia dolor sit amet, consectetur velit.</p><a>READ MORE</a></div>
    <div class="course"><div class="head"><svg width="30" height="30" viewBox="0 0 30 30"><circle cx="15" cy="15" r="13" fill="none" stroke="#e0902c" stroke-width="3"/><path d="M9 15l4.5 4.5L21.5 11" stroke="#e0902c" stroke-width="3" fill="none"/></svg><h3>Keyboard &amp;<br>Typing</h3></div><p>Neque porro quisquam est qui dolorem ipsum quia dolor sit amet, consectetur velit.</p><a>READ MORE</a></div>
    <div class="course"><div class="head"><svg width="30" height="30" viewBox="0 0 30 30"><circle cx="15" cy="15" r="13" fill="none" stroke="#e0902c" stroke-width="3"/><path d="M9 15l4.5 4.5L21.5 11" stroke="#e0902c" stroke-width="3" fill="none"/></svg><h3>Calder Online</h3></div><p>Neque porro quisquam est qui dolorem ipsum quia dolor sit amet, consectetur velit.</p><a>READ MORE</a></div>
    <div class="course"><div class="head"><svg width="30" height="30" viewBox="0 0 30 30"><circle cx="15" cy="15" r="13" fill="none" stroke="#e0902c" stroke-width="3"/><path d="M9 15l4.5 4.5L21.5 11" stroke="#e0902c" stroke-width="3" fill="none"/></svg><h3>Confidentiality</h3></div><p>Neque porro quisquam est qui dolorem ipsum quia dolor sit amet, consectetur velit.</p><a>READ MORE</a></div>
  </div>
</section>

<section class="why">
  <h2 class="sec-title">Why Calder Institute?</h2>
  <div class="feature" style="left:75px;top:132px;width:510px;height:126px">
    <h3>Quality</h3>
    <p>Calder delivery quality, effective training facilitated by industry leaders. Just ask our students who rate us on average.</p>
    <svg width="62" height="62" viewBox="0 0 62 62" fill="none" stroke="#e0902c" stroke-width="3"><rect x="4" y="14" width="42" height="42"/><path d="M14 32l10 10L56 6"/></svg>
  </div>
  <div class="feature" style="left:75px;top:285px;width:510px;height:114px">
    <h3>Experience</h3>
    <p>Calder is Australia's largest and leading provider of nationally recognised training in health administration. [...]</p>
    <svg width="64" height="52" viewBox="0 0 64 52" fill="#e0902c"><circle cx="32" cy="12" r="9"/><circle cx="12" cy="20" r="7"/><circle cx="52" cy="20" r="7"/><path d="M18 50c0-12 6-20 14-20s14 8 14 20z"/><path d="M0 48c0-9 5-15 12-15 4 0 7 2 9 5-3 3-4 7-5 10z"/><path d="M64 48c0-9-5-15-12-15-4 0-7 2-9 5 3 3 4 7 5 10z"/></svg>
  </div>
  <div class="feature" style="left:75px;top:426px;width:510px;height:114px">
    <h3>Value</h3>
    <p>Our innovative teaching approach allows us to deliver exceptional training at affordable prices. [...]</p>
    <svg width="64" height="52" viewBox="0 0 64 52" fill="none" stroke="#e0902c" stroke-width="2.5"><path d="M14 3h36l12 15L32 49 2 18z"/><path d="M2 18h60M22 3l-6 15 16 31 16-31-6-15"/></svg>
  </div>
  <div class="feature" style="left:628px;top:141px;width:499px;height:135px">
    <h3>Industry Recognised</h3>
    <p>Calder work hand in hand with industry to develop our core programme and consolidate the programme annually to keep the programme fresh and relevant.</p>
    <svg width="64" height="58" viewBox="0 0 64 58" fill="none" stroke="#e0902c" stroke-width="2.5"><path d="M4 56V26l14 9V26l14 9V26l14 9V6h10v50z"/><path d="M14 44h6M28 44h6M42 44h6"/></svg>
  </div>
  <div class="feature" style="left:628px;top:312px;width:499px;height:141px">
    <h3>Great Job Results</h3>
    <p>Calder students get jobs! Our focus is to create job-ready students who are mentored to achieve their goals. Calder also provide a recruitment service for industry &amp; graduates.</p>
    <svg width="60" height="64" viewBox="0 0 60 64" fill="none" stroke="#e0902c" stroke-width="3"><path d="M4 6h52v40L42 60H4z"/><path d="M42 60V46h14M16 30l9 9 18-20"/></svg>
  </div>
</section>

<section class="blog">
  <h2 class="sec-title">Latest Blog Roll</h2>
  <div class="blog-box">
    <div class="scroll"><i></i></div>
    <div class="post" style="left:15px;top:25px"><div class="thumb" role="img" aria-label="Portrait photo for blog post"></div><div class="body"><h4>De finebus lato</h4><p>Neque porro quisquam est qui dolorem ipsum quia dolor sit amet, consectetur velit.</p><div class="meta"><span>June 23, 2016</span><span>✎ (0)</span></div></div></div>
    <div class="post" style="left:357px;top:25px"><div class="thumb" role="img" aria-label="Portrait photo for blog post" style="background:linear-gradient(135deg,#8fb3cf,#dbe7f0)"></div><div class="body"><h4>De finebus lato</h4><p>Neque porro quisquam est qui dolorem ipsum quia dolor sit amet, consectetur velit.</p><div class="meta"><span>June 23, 2016</span><span>✎ (0)</span></div></div></div>
    <div class="post" style="left:700px;top:25px"><div class="thumb" role="img" aria-label="Portrait photo for blog post" style="background:linear-gradient(135deg,#e0a86f,#f4dcc0)"></div><div class="body"><h4>De finebus lato</h4><p>Neque porro quisquam est qui dolorem ipsum quia dolor sit amet, consectetur velit.</p><div class="meta"><span>June 23, 2016</span><span>✎ (0)</span></div></div></div>
    <div class="post" style="left:15px;top:200px"><div class="thumb" role="img" aria-label="Photo of a person reading for blog post" style="background:linear-gradient(135deg,#8a95a8,#d6dbe3)"></div><div class="body"><h4>De finebus lato</h4><p>Neque porro quisquam est qui dolorem ipsum quia dolor sit amet, consectetur velit.</p><div class="meta"><span>June 23, 2016</span><span>✎ (0)</span></div></div></div>
    <div class="post" style="left:357px;top:200px"><div class="thumb" role="img" aria-label="Portrait photo for blog post" style="background:linear-gradient(135deg,#b79a82,#ead9c8)"></div><div class="body"><h4>De finebus lato</h4><p>Neque porro quisquam est qui dolorem ipsum quia dolor sit amet, consectetur velit.</p><div class="meta"><span>June 23, 2016</span><span>✎ (0)</span></div></div></div>
    <div class="post" style="left:700px;top:200px"><div class="thumb" role="img" aria-label="Portrait photo for blog post" style="background:linear-gradient(135deg,#7b6f68,#cfc6bf)"></div><div class="body"><h4>De finebus lato</h4><p>Neque porro quisquam est qui dolorem ipsum quia dolor sit amet, consectetur velit.</p><div class="meta"><span>June 23, 2016</span><span>✎ (0)</span></div></div></div>
  </div>
</section>

<section class="enquiry">
  <div class="enquiry-bg" role="img" aria-label="Warm orange background photo behind the enquiry form"></div>
  <h2 class="sec-title">Make An Enquiry</h2>
  <div class="field" style="left:222px;top:152px"><i></i>Enter Name</div>
  <div class="field" style="left:478px;top:152px"><i></i>Enter Email</div>
  <div class="field" style="left:735px;top:152px"><i></i>Enter Course Name</div>
  <div class="field" style="left:222px;top:211px"><i></i>Enter State Name</div>
  <div class="field" style="left:478px;top:211px"><i></i>Enter Mobile No.</div>
  <a class="btn btn-navy">Submit Here</a>
</section>

<section class="testimonials">
  <h2 class="sec-title">Testimonials</h2>
  <div class="quote">I want to say a huge thank you for the course and knowledge I came away with. I have secured a fantastic job after my first application! Such good value for money too! I would highly recommend it. I'm a mature age person so it's never too late to up-skill yourself to get what you deserve!</div>
  <span class="arrow" style="left:475px">‹</span>
  <span class="arrow" style="left:716px">›</span>
  <div class="person"><div class="avatar" role="img" aria-label="Portrait photo of the reviewer"></div><div class="name">Mia Harlow</div></div>
</section>

<footer class="footer">
  <div class="col" style="left:75px;width:240px">
    <h5>About</h5>
    <div class="foot-brand"><div class="mark"></div><div class="name">Calder Institute of Training</div></div>
    <p style="margin-top:18px">Lorem Ipsum is simply dummy text of the printing and typesetting industry. Lorem Ipsum has been industry's.</p>
    <div class="social" style="position:static;margin-top:10px;color:#c4cbd9"><span></span><span></span><span></span><span></span><span></span></div>
  </div>
  <div class="col" style="left:360px;width:230px">
    <h5>Latest Posts</h5>
    <ul style="margin-top:28px">
      <li>Sed ut perspiciatis unde omni iste natus error sit voluptatem</li><li class="date">JUNE 21, 2016</li>
      <li>Sed ut perspiciatis unde omni iste natus error sit voluptatem</li><li class="date">JUNE 21, 2016</li>
      <li>Sed ut perspiciatis unde omni iste natus error sit voluptatem</li><li class="date">JUNE 21, 2016</li>
    </ul>
  </div>
  <div class="col" style="left:635px;width:230px">
    <h5>JV Updates</h5>
    <ul style="margin-top:28px">
      <li>"Lorem Ipsum is simply dummy text of the printing and typesetting industry. lorem Ipsum has industry's."</li><li class="date">3 MONTH AGO</li>
      <li>"Lorem Ipsum is simply dummy text of the printing and typesetting industry. lorem Ipsum has industry's."</li><li class="date">3 MONTH AGO</li>
    </ul>
  </div>
  <div class="col" style="left:910px;width:240px">
    <h5>Contact</h5>
    <p style="margin-top:22px">48 Tanner Street,<br>Milton QLD 4064</p>
    <p style="margin-top:12px">Call: 07 3000 0000<br>Email: info@calderinstitute.example</p>
    <h5 style="margin-top:28px">Newsletter</h5>
    <p style="margin-top:8px">By subscribing you will get the latest news from us</p>
    <div class="newsletter"><div class="input">Enter Email</div><div class="go"><svg width="10" height="12" viewBox="0 0 10 12"><path d="M0 0l10 6-10 6z" fill="#fff"/></svg></div></div>
  </div>
  <div class="copyright">Copyright © 2016, Calder Health. All rights reserved.</div>
</footer>

</body>
</html>
```